Patent Law

Need to develop a home page for a patent lawyer.

Colors should go with logo, blues...

Company Name- Velun Tresk, PLLC

Company Overview-

I am an Intellectual Property Lawyer and focus on patents, copyrights, trademarks, & trade secrets. I work with small businesses and start ups in the chemical and biotech industries.

Why Us-

I am small firm that can provide large-firm service at a reasonable price. I also can charge flat-fees for entreprenuers in certain practice areas.

Services-
Intellectual Property
Patents
Copyrights
Trademarks
Trade secrets
Healthcare Compliance
Elder law
Wills
Trusts

Website we like-
http://www.quorvantlegal.example/ - within industry!!
http://www.daltrowemiko.example/
http://ulbrixtane.example/
http://thegravelcounsel.example/

Target Market(s)

My customers will be small business, specifically small start-up companies in the chemical and biotech arena.

Industry/Entity Type

Trade

Requirements
Must have
• Colors should go with logo, blues...

```html
<!DOCTYPE html>
<html lang="en">
<head>
<meta charset="utf-8">
<title>Velun Tresk, PLLC — Intellectual Property Law</title>
<link rel="stylesheet" href="https://fonts.googleapis.com/css2?family=Open+Sans:wght@400;600;700&family=Cinzel:wght@400&display=swap">
<style>
  :root{
    --dark:#25282b;
    --nav-blue:#1ba3e0;
    --col-1:#0a82cc;
    --col-2:#1371bb;
    --col-3:#0a5c9f;
    --caption:rgba(62,67,71,.9);
    --arrow:#1d6fa6;
    --white:#ffffff;
    --logo-grey:#4c5257;
    --footer-text:#e7e9eb;
  }
  *{margin:0;padding:0;box-sizing:border-box}
  html,body{width:1200px;height:1157px;overflow:hidden;background:var(--white)}
  body{position:relative;font-family:"Open Sans",Arial,sans-serif;color:var(--white)}
  a{color:inherit;text-decoration:none}

  .hero-photo{position:absolute;left:0;top:0;width:1200px;height:583px;
    background:linear-gradient(90deg,#1b2030 0%,#2a3550 30%,#3b4f7a 50%,#c9ccd4 72%,#f4f4f5 88%,#ffffff 100%)}
  .top-bar{position:absolute;left:0;top:0;width:1200px;height:59px;background:var(--dark)}
  .top-contact{position:absolute;top:19px;display:flex;align-items:center;gap:11px;font-size:12.5px}
  .top-contact .icon-box{width:24px;height:24px;border:1px solid var(--nav-blue);display:flex;align-items:center;justify-content:center}
  .nav-band{position:absolute;left:0;top:59px;width:1200px;height:70px;background:var(--nav-blue)}
  .main-nav{position:absolute;top:77px;left:502px;display:flex;font-weight:700;font-size:13.5px}
  .main-nav a{height:35px;line-height:33px;padding:0 18px;margin-right:-1px;border:1px solid transparent}
  .main-nav a.current{border-color:var(--white)}
  .main-nav a:not(:first-child){padding:0 16.5px}

  .brand-plate{position:absolute;left:161px;top:0;width:227px;height:230px}
  .brand-plate .name{position:absolute;left:0;top:118px;width:227px;text-align:center;font-family:"Cinzel",Georgia,serif;font-size:17px;color:var(--logo-grey);letter-spacing:.5px}
  .brand-plate .mark{position:absolute;left:96px;top:40px;width:36px;height:36px;border-radius:50%;background:var(--nav-blue)}

  .caption-bar{position:absolute;left:0;top:502px;width:1200px;height:81px;background:var(--caption)}
  .caption-bar p{position:absolute;left:0;width:1200px;top:31px;text-align:center;font-weight:700;font-size:15px}
  .slide-arrow{position:absolute;top:0;width:35px;height:81px;background:var(--arrow);display:flex;align-items:center;justify-content:center}

  .feature-row{position:absolute;left:161px;top:640px;width:877px;height:335px;display:flex}
  .feature{position:relative;height:335px;padding:28px 0 0 34px}
  .feature.why{width:293px;background:var(--col-1)}
  .feature.services{width:293px;background:var(--col-2)}
  .feature.contact{width:291px;background:var(--col-3)}
  .feature h2{display:flex;align-items:center;gap:14px;font-size:25.5px;font-weight:700;height:30px}
  .feature .body{margin-top:27px;font-size:12.5px;line-height:19px;width:226px}
  .feature ul{list-style:none;margin-top:25px;font-size:12.5px}
  .feature li{display:flex;align-items:center;gap:10px;height:26.6px}
  .feature .more{position:absolute;left:34px;top:268px;width:93px;height:38px;border:1px solid var(--white);text-align:center;line-height:36px;font-weight:700;font-size:14.5px}

  .site-footer{position:absolute;left:0;top:1034px;width:1200px;height:123px;background:var(--dark);color:var(--footer-text)}
  .footer-nav{position:absolute;left:161px;top:36px;font-size:12.5px;display:flex}
  .footer-nav a+a::before{content:"|";margin:0 11px;font-size:11px}
  .copyright{position:absolute;left:161px;top:61px;font-size:12.5px}
  .social{position:absolute;left:845px;top:42px;display:flex;gap:7px}
  .social span{width:26px;height:26px;border:1px solid var(--white)}
  .social span.filled{background:var(--nav-blue);border-color:var(--nav-blue)}
  .footer-brand{position:absolute;left:921px;top:76px;font-family:"Cinzel",Georgia,serif;font-size:12px;color:#6d7378}
</style>
</head>
<body>

<div class="hero-photo" role="img" aria-label="Lawyer in a dark suit and blue tie holding brass scales of justice and a wooden gavel"></div>

<header>
  <div class="top-bar"></div>
  <div class="top-contact" style="left:835px">
    <span class="icon-box"><svg width="12" height="12" viewBox="0 0 24 24"><path fill="#1ba3e0" d="M6.6 10.8a15 15 0 006.6 6.6l2.2-2.2c.3-.3.7-.4 1-.2 1.1.4 2.3.6 3.6.6.6 0 1 .4 1 1V20c0 .6-.4 1-1 1A17 17 0 013 4c0-.6.4-1 1-1h3.5c.6 0 1 .4 1 1 0 1.3.2 2.5.6 3.6.1.3 0 .7-.2 1z"/></svg></span>
    <span>+00 555-014-272</span>
  </div>
  <div class="top-contact" style="left:979px">
    <span class="icon-box"><svg width="10" height="13" viewBox="0 0 20 26"><path fill="#1ba3e0" d="M10 0a9 9 0 00-9 9c0 7 9 17 9 17s9-10 9-17a9 9 0 00-9-9zm0 12.5A3.5 3.5 0 1110 5.5a3.5 3.5 0 010 7z"/></svg></span>
    <span>MAP</span>
  </div>
  <div class="nav-band"></div>
  <nav class="main-nav">
    <a class="current" href="#">HOME</a>
    <a href="#">ABOUT US</a>
    <a href="#">SERVICES</a>
    <a href="#">PRACTICES</a>
    <a href="#">NEWS</a>
    <a href="#">CONTACT US</a>
  </nav>
  <div class="brand-plate">
    <svg width="227" height="230" viewBox="0 0 227 230" style="position:absolute;left:0;top:0"><polygon points="0,0 227,0 227,167 113.5,230 0,167" fill="#ffffff"/></svg>
    <span class="mark"></span>
    <span class="name">VELUN TRESK, PLLC</span>
  </div>
</header>

<section class="caption-bar">
  <a class="slide-arrow" href="#" style="left:161px"><svg width="12" height="20" viewBox="0 0 12 20"><path d="M10 2L2 10l8 8" stroke="#fff" stroke-width="2.5" fill="none"/></svg></a>
  <p>I FOCUS ON PATENTS, COPYRIGHTS, TRADEMARKS, &amp; TRADE SECRETS.</p>
  <a class="slide-arrow" href="#" style="left:1004px"><svg width="12" height="20" viewBox="0 0 12 20"><path d="M2 2l8 8-8 8" stroke="#fff" stroke-width="2.5" fill="none"/></svg></a>
</section>

<main class="feature-row">
  <article class="feature why">
    <h2><span style="font-size:34px;line-height:1">?</span>WHY US</h2>
    <p class="body">Lorem Ipsum is simply dummy text of the printing and typesetting industry. Lorem Ipsum has been the industry's standard dummy text ever since the 1500s, when an unknown printer took a galley of type and scrambled it to make a type specimen book. It has survived not only five centuries.</p>
    <a class="more" href="#">MORE</a>
  </article>
  <article class="feature services">
    <h2><svg width="30" height="30" viewBox="0 0 30 30"><g fill="#fff"><rect x="3" y="6" width="14" height="9" transform="rotate(-40 10 10)"/><rect x="13" y="14" width="4" height="16" transform="rotate(-40 15 22)"/></g></svg>SERVICES</h2>
    <ul>
      <li><svg width="5" height="8"><path d="M0 0l5 4-5 4z" fill="#fff"/></svg>Intellectual Property</li>
      <li><svg width="5" height="8"><path d="M0 0l5 4-5 4z" fill="#fff"/></svg>Patents</li>
      <li><svg width="5" height="8"><path d="M0 0l5 4-5 4z" fill="#fff"/></svg>Copyrights</li>
      <li><svg width="5" height="8"><path d="M0 0l5 4-5 4z" fill="#fff"/></svg>Trademarks</li>
      <li><svg width="5" height="8"><path d="M0 0l5 4-5 4z" fill="#fff"/></svg>Trade secrets</li>
      <li><svg width="5" height="8"><path d="M0 0l5 4-5 4z" fill="#fff"/></svg>Healthcare Compliance</li>
    </ul>
    <a class="more" href="#">MORE</a>
  </article>
  <article class="feature contact">
    <h2><svg width="18" height="27" viewBox="0 0 20 28"><path fill="#fff" d="M10 0a9.5 9.5 0 00-9.5 9.5C.5 17 10 28 10 28s9.5-11 9.5-18.5A9.5 9.5 0 0010 0zm0 13.5a4 4 0 110-8 4 4 0 010 8z"/></svg>CONTACT US</h2>
    <ul>
      <li><svg width="13" height="11" viewBox="0 0 13 11"><path d="M6.5 0L0 5.5h2V11h3.5V7.5h2V11H11V5.5h2z" fill="#fff"/></svg>VELUN TRESK, PLLC</li>
      <li><svg width="8" height="11" viewBox="0 0 20 28"><path fill="#fff" d="M10 0a9.5 9.5 0 00-9.5 9.5C.5 17 10 28 10 28s9.5-11 9.5-18.5A9.5 9.5 0 0010 0zm0 13.5a4 4 0 110-8 4 4 0 010 8z"/></svg>Address :&nbsp; Lorem Ipsum is simply</li>
      <li><svg width="11" height="11" viewBox="0 0 24 24"><path fill="#fff" d="M6.6 10.8a15 15 0 006.6 6.6l2.2-2.2c.3-.3.7-.4 1-.2 1.1.4 2.3.6 3.6.6.6 0 1 .4 1 1V20c0 .6-.4 1-1 1A17 17 0 013 4c0-.6.4-1 1-1h3.5c.6 0 1 .4 1 1 0 1.3.2 2.5.6 3.6.1.3 0 .7-.2 1z"/></svg>+00 555-014-272</li>
      <li><svg width="11" height="11" viewBox="0 0 24 24"><path fill="#fff" d="M6.6 10.8a15 15 0 006.6 6.6l2.2-2.2c.3-.3.7-.4 1-.2 1.1.4 2.3.6 3.6.6.6 0 1 .4 1 1V20c0 .6-.4 1-1 1A17 17 0 013 4c0-.6.4-1 1-1h3.5c.6 0 1 .4 1 1 0 1.3.2 2.5.6 3.6.1.3 0 .7-.2 1z"/></svg>+ 0055-501-48</li>
      <li><svg width="13" height="10" viewBox="0 0 13 10"><rect width="13" height="10" fill="#fff"/><path d="M0 0l6.5 5L13 0" stroke="#0a5c9f" fill="none"/></svg>info@velunlaw.example</li>
    </ul>
    <a class="more" href="#">MORE</a>
  </article>
</main>

<footer class="site-footer">
  <nav class="footer-nav">
    <a href="#">Home</a><a href="#">About Us</a><a href="#">Services</a><a href="#">Practices</a><a href="#">News</a><a href="#">Contact us</a>
  </nav>
  <p class="copyright">Copyright © 2014 Velun Tresk pllc.</p>
  <div class="social"><span class="filled"></span><span></span><span></span></div>
  <span class="footer-brand">VELUN TRESK, PLLC</span>
</footer>

</body>
</html>
```